Academic and Business book cover

I need a book cover for my academic and business book.
The focus is in international / global negotiation and influence (how to negotiate across cultures).
The book will be published on Zelvorn, both in Vaspet and printed edition. therefore I need something that works under Zelvorn guidelines.The final design should be elegant and still be able to stand out against the competition.
I would like to have orange+grey for the text colors on the cover, even if different options are welcome.
Title and my name are in the attached word doc.

Target Market(s)

graduates, Phds, from international business schools. Managers

Industry/Entity Type

Business

Font styles to use
Serif
Sans Serif

Colors

Designer to choose colors to be used in the design.

Requirements
Must have
• The title and my name should have elegant fonts.
Nice to have
• pictures of the world that don't have the "usual" Europe in the centre.

```html
<!DOCTYPE html>
<html lang="en">
<head>
<meta charset="utf-8">
<title>The 5Cs Compass – Book Cover</title>
<link href="https://fonts.googleapis.com/css2?family=Arimo:wght@400;500;600;700&display=swap" rel="stylesheet">
<style>
  :root {
    --page: #ffffff;
    --cover: #0d1117;
    --orange: #f6a21d;
    --text-light: #e9ebee;
    --grey-block: #353a43;
    --art-green: #4f9a2a;
    --art-lime: #a8d62a;
    --art-blue: #2a5aa6;
    --art-violet: #7a3a82;
  }
  html, body {
    margin: 0;
    width: 1200px;
    height: 1000px;
    overflow: hidden;
    background: var(--page);
    font-family: "Arimo", Arial, sans-serif;
  }
  .cover-wrap {
    position: absolute;
    left: 62px;
    top: 105px;
    width: 1093px;
    height: 822px;
    background: var(--cover);
    box-shadow: 6px 8px 18px rgba(0,0,0,0.35);
  }
  .back-rule {
    position: absolute;
    left: 38px;
    top: 84px;
    width: 437px;
    height: 3px;
    background: var(--orange);
  }
  .back-copy {
    position: absolute;
    left: 38px;
    width: 437px;
    color: var(--text-light);
    font-size: 10.6px;
    font-weight: 600;
    line-height: 19.6px;
    text-align: justify;
    hyphens: auto;
    margin: 0;
  }
  .back-blurb { top: 101px; }
  .back-blurb p { margin: 0; }
  .back-bio { top: 333px; }
  .back-bio .author-inline { color: var(--orange); }

  .spine {
    position: absolute;
    left: 522px;
    top: 72px;
    width: 60px;
    height: 730px;
  }
  .spine-text {
    position: absolute;
    writing-mode: vertical-rl;
    white-space: nowrap;
    font-weight: 700;
  }
  .spine-title { left: 14px; top: 2px; color: var(--orange); font-size: 23px; }
  .spine-subtitle { left: 2px; top: 264px; color: var(--text-light); font-size: 15px; line-height: 19px; font-weight: 600; }
  .spine-author { left: 14px; top: 555px; color: var(--orange); font-size: 20px; }

  .front {
    position: absolute;
    left: 563px;
    top: 0;
    width: 530px;
    height: 822px;
  }
  .title-block {
    position: absolute;
    top: 75px;
    width: 49px;
    height: 49px;
    background: var(--grey-block);
  }
  .title-block.left { left: 17px; }
  .title-block.right { right: 0; }
  .front-title {
    position: absolute;
    left: 0; right: 0;
    top: 82px;
    margin: 0;
    text-align: center;
    color: var(--orange);
    font-size: 37px;
    font-weight: 700;
    padding-left: 18px;
  }
  .front-subtitle {
    position: absolute;
    left: 0; right: 0;
    top: 146px;
    margin: 0;
    text-align: center;
    color: var(--text-light);
    font-size: 26.5px;
    font-weight: 600;
    line-height: 40px;
    padding-left: 18px;
  }
  .cover-art {
    position: absolute;
    left: 17px;
    top: 259px;
    width: 513px;
    height: 467px;
    background: linear-gradient(160deg, var(--art-lime) 0%, var(--art-green) 40%, var(--art-blue) 75%, var(--art-violet) 100%);
    opacity: 0.85;
  }
  .front-author {
    position: absolute;
    left: 0; right: 0;
    top: 756px;
    margin: 0;
    text-align: center;
    color: var(--orange);
    font-size: 28px;
    font-weight: 700;
    padding-left: 18px;
  }
</style>
</head>
<body>
  <div class="cover-wrap">
    <section class="back-cover">
      <div class="back-rule"></div>
      <div class="back-copy back-blurb">
        <p>Western notions of negotiation and influence are coming under question: old familiar concepts, such as power, <em>interests</em>, and above all, <em>BATNA</em>, take on different meanings in an international context.</p>
        <p>Adopting an interdisciplinary approach and staying away from academic jargon, and conventional generalizations, the book is meant to provide graduates and managers with a framework for negotiating and influencing across cultures.</p>
        <p>The goal is to overcome Western (particularly US) ethnocentrism, moving out of laboratory simulations and providing a model based on real life exposure to international negotiations and managerial challenges.</p>
      </div>
      <p class="back-copy back-bio"><span class="author-inline">Tarvin K. Solan</span> is Professor of Cultural Management at the Meridian University in Milan, Italy, and founder of Tralvex, a management consultancy firm that assists companies in international negotiations and global teams performance improvement. He has previously lived and worked in eight countries and four different continents, leading cross functional teams implementing post M&amp;A integration strategies and managing commercial and marketing organizations in Europe, North &amp; South America, Middle East and South &amp; East Asia.</p>
    </section>

    <section class="spine">
      <span class="spine-text spine-title">The 5Cs Compass</span>
      <span class="spine-text spine-subtitle">Strategic Negotiation and Persuasion<br>Approaches for Worldwide Impact</span>
      <span class="spine-text spine-author">Tarvin K. Solan</span>
    </section>

    <section class="front">
      <div class="title-block left"></div>
      <div class="title-block right"></div>
      <h1 class="front-title">The 5Cs Compass</h1>
      <h2 class="front-subtitle">Strategic Negotiation and Persuasion<br>Approaches for Worldwide Impact</h2>
      <div class="cover-art" role="img" aria-label="Cover illustration: a world globe framed by overlapping translucent coloured bands"></div>
      <p class="front-author">Tarvin K. Solan</p>
    </section>
  </div>
</body>
</html>
```